Manufacturer's Representative Group needs a clean new Website

We represent and sell a number of suppliers that design and build products used in Biopharmaceutical manufacturing. Our sales region is in the central US. Our customer base is scientific / engineering based - so clean, we organized design with a focus on the products - easy and clear navigation is necessary. We do not sell direct or warehouse product - so e-commerce is not needed. Our customers will use the website for reference on what we do and offer - we will use the site as a platform to present products from each vendor and the home page will be used to capture an overview and draw users deeper into the site. You can view our current site - which needs A LOT of help to get ideas on products represented and types of products

Target Market(s)

Engineers and Pharmaceutical / Bio pharm end users

Industry/Entity Type

E-Commerce

Number of Pages Required

2 page

Font styles to use
Sans Serif

Requirements
Must have
• I need a home page that provides a snapshot of my company and the product lines we represent - then a second page that I can copy as a template for each line I rep as well as for an "About us / contact" page.
• I would like to be able to manage content on the pages so something easy to adjust pictures or add content is a must
• Must use our logo

```html
<!DOCTYPE html>
<html lang="en">
<head>
<meta charset="utf-8">
<title>Prairie Bio — Home</title>
<link href="https://fonts.googleapis.com/css2?family=Raleway:wght@300;500;600&family=Roboto:wght@300;400;500&display=swap" rel="stylesheet">
<style>
:root{
  --navy:#2b2563;
  --orange:#f05a28;
  --dark:#333333;
  --field:#555555;
  --white:#ffffff;
  --ink:#222222;
  --line:#dddddd;
}
*{box-sizing:border-box;margin:0;padding:0}
html,body{width:867px;height:1200px;overflow:hidden}
body{position:relative;background:var(--white);font-family:'Roboto',sans-serif;color:var(--ink)}
.abs{position:absolute}
.brand{display:flex;align-items:center;gap:7px;font-family:'Raleway',sans-serif;font-weight:500;font-size:21px;color:var(--navy)}
.brand .dot{width:14px;height:14px;border-radius:50%;background:var(--orange)}
.site-header{left:0;top:0;width:867px;height:76px;background:linear-gradient(90deg,#ffffff,#eef0f4)}
.helpline{left:528px;top:22px;width:249px;height:36px;background:#fff;border:1px solid #ddd;border-radius:2px;font-size:9px;line-height:11.5px;color:var(--navy);padding:6px 0 0 48px}
.helpline .agent{position:absolute;left:10px;top:1px;width:30px;height:34px;background:linear-gradient(#c9a88a,#5a4a44);border-radius:3px}
.helpline b{color:var(--orange);font-weight:400}
.main-nav{left:0;top:76px;width:867px;height:45px;background:var(--navy)}
.main-nav a{position:absolute;top:17px;font-size:9.5px;color:#fff;text-decoration:none;letter-spacing:.1px}
.main-nav a.active{color:var(--orange)}
.social{display:flex;gap:14px}
.social span{width:15px;height:15px;border-radius:50%;background:#fff}
.search{left:649px;top:89px;width:128px;height:19px;background:#fff}
.hero{left:0;top:121px;width:867px;height:266px;background:linear-gradient(100deg,#dfe6ee 0%,#b9cde2 35%,#2f5ea8 60%,#c7d9ea 85%,#9fb8d4 100%)}
.about{left:0;top:387px;width:867px;height:158px;background:var(--orange)}
.sec-title{font-family:'Raleway',sans-serif;font-weight:500;font-size:18px;padding-bottom:4px;display:inline-block}
.rule{position:absolute;height:1px}
.rule::after{content:"";position:absolute;right:0;top:-3px;width:5px;height:5px;border-top:1px solid currentColor;border-right:1px solid currentColor;transform:rotate(45deg)}
.about p{left:90px;top:64px;width:572px;font-size:10px;line-height:13px;color:#fff}
.about p em{font-style:normal;color:var(--navy)}
.btn-navy{left:678px;top:75px;width:99px;height:24px;background:var(--navy);color:#fff;font-size:10px;display:flex;align-items:center;justify-content:center}
.card{top:627px;width:158px;height:196px;background:var(--navy);border:1px solid #ccc;text-align:center;color:#fff}
.card .photo{height:80px}
.card h3{font-weight:400;font-size:14px;margin-top:11px}
.card p{font-size:7.6px;line-height:11.5px;padding:5px 12px 0;color:#e6e6f0}
.card .more{position:absolute;left:39px;top:160px;width:79px;height:17px;background:var(--orange);font-size:7.5px;font-weight:500;display:flex;align-items:center;justify-content:center}
.card .overlay{position:absolute;left:8px;top:10px;width:141px;height:176px;background:rgba(240,90,40,.85)}
.overlay .ttl{font-family:'Raleway',sans-serif;font-weight:300;font-size:19px;line-height:21px;margin-top:20px;color:#fff}
.overlay .icons{position:absolute;left:45px;top:90px;display:flex;gap:6px}
.overlay .icons span{width:26px;height:26px;border-radius:50%;background:#fff;display:flex;align-items:center;justify-content:center}
.arrow{width:31px;height:31px;background:var(--navy);display:flex;align-items:center;justify-content:center}
.partners{left:94px;top:915px;display:flex;gap:7px}
.partners div{width:88px;height:36px;border:1px solid #e2e2e2;display:flex;align-items:center;justify-content:center;font-size:9.5px;font-weight:500;color:var(--navy);text-align:center}
.footer{left:0;top:983px;width:867px;height:217px;background:var(--dark);color:#fff}
.footer .brand{color:#fff}
.person{top:22px;width:99px;text-align:center}
.person .photo{height:110px}
.person h4{font-weight:400;font-size:13px;margin-top:15px}
.person .line{font-size:8.5px;margin-top:6px;display:flex;gap:5px;justify-content:center;align-items:center}
.field{background:var(--field);font-size:8.5px;color:#fff;padding:9px 8px}
.send{background:var(--orange);font-size:11px;display:flex;align-items:center;justify-content:center}
</style>
</head>
<body>

<header class="site-header abs">
  <div class="brand abs" style="left:90px;top:28px"><span class="dot"></span>Prairie Bio</div>
  <div class="helpline abs"><span class="agent" role="img" aria-label="Support agent with headset"></span>Need a helping hand? Call our office search<br>helpline for advice - <b>+1 5550142210</b></div>
</header>

<nav class="main-nav abs">
  <a class="active" style="left:90px">HOME</a>
  <a style="left:142px">ABOUT US</a>
  <a style="left:213px">OUR PRODUCTS</a>
  <a style="left:307px">MANUFATUR LINK</a>
  <a style="left:410px">CONTACT</a>
  <div class="social abs" style="left:512px;top:15px"><span></span><span></span><span></span><span></span><span></span></div>
  <div class="search abs" style="top:13px">
    <svg class="abs" style="right:6px;top:4px" width="11" height="11" viewBox="0 0 11 11"><circle cx="4.5" cy="4.5" r="3.3" fill="none" stroke="#222" stroke-width="1.6"/><line x1="7" y1="7" x2="10" y2="10" stroke="#222" stroke-width="1.8"/></svg>
  </div>
</nav>

<div class="hero abs" role="img" aria-label="Laboratory scene with a gloved hand pipetting into a vial beside glass flasks"></div>

<section class="about abs">
  <div class="abs" style="left:90px;top:30px;color:#fff"><h2 class="sec-title">About us</h2></div>
  <div class="rule abs" style="left:90px;top:50px;width:136px;background:#fff;color:#fff"></div>
  <p class="abs"><em>Prairie Biosolutions</em> is a distribution channel, licensed partner and manufacturers representative group providing high quality fluid handling products and technical services to the Midwestern biopharmaceutical community. With a core staff of experienced professionals and a team approach to all customer needs, we offer over 30 years of cGMP experience in the selection and use of most process consumable products. We're looking forward to working with you!</p>
  <div class="btn-navy abs">READ MORE</div>
</section>

<section>
  <div class="abs" style="left:90px;top:571px;color:var(--navy)"><h2 class="sec-title">Our Products</h2></div>
  <div class="rule abs" style="left:90px;top:595px;width:134px;background:var(--navy);color:var(--navy)"></div>

  <div class="arrow abs" style="left:40px;top:701px"><svg width="8" height="12" viewBox="0 0 8 12"><path d="M6 1 1 6l5 5" fill="none" stroke="#fff" stroke-width="1.5"/></svg></div>
  <div class="arrow abs" style="left:796px;top:701px"><svg width="8" height="12" viewBox="0 0 8 12"><path d="M2 1l5 5-5 5" fill="none" stroke="#fff" stroke-width="1.5"/></svg></div>

  <article class="card abs" style="left:90px">
    <div class="photo" style="background:linear-gradient(#8a6a5a,#c0392b)" role="img" aria-label="Peristaltic pump unit"></div>
    <h3>Tamworth Pump</h3>
    <p>Lorem ipsum dolor sit amet, consect-etur adipisicing elit, sed do eiusmod tempor incididunt ut labore.</p>
    <div class="more">READ MORE</div>
    <div class="overlay">
      <div class="ttl">Tamworth<br>Pumps</div>
      <div class="icons">
        <span><svg width="10" height="12" viewBox="0 0 10 12"><path d="M1 0h5l3 3v9H1z" fill="var(--navy)"/></svg></span>
        <span><svg width="12" height="12" viewBox="0 0 12 12"><rect x="1" y="5" width="6" height="3" rx="1.5" transform="rotate(-45 4 6.5)" fill="none" stroke="var(--navy)" stroke-width="1.5"/><rect x="5" y="4" width="6" height="3" rx="1.5" transform="rotate(-45 8 5.5)" fill="none" stroke="var(--navy)" stroke-width="1.5"/></svg></span>
      </div>
    </div>
  </article>

  <article class="card abs" style="left:267px">
    <div class="photo" style="background:linear-gradient(#f4f4f4,#b8b8b8)" role="img" aria-label="Automated liquid filling machine"></div>
    <h3>Fillwell FP50</h3>
    <p>Lorem ipsum dolor sit amet, consect-etur adipisicing elit, sed do eiusmod tempor incididunt ut labore.</p>
    <div class="more">READ MORE</div>
  </article>

  <article class="card abs" style="left:443px">
    <div class="photo" style="background:linear-gradient(90deg,#3a8fd0,#b9c2ca 40%,#dfe8ef 70%,#3a8fd0)" role="img" aria-label="Braided hose with helical wire reinforcement"></div>
    <h3>Helical wire</h3>
    <p>Lorem ipsum dolor sit amet, consect-etur adipisicing elit, sed do eiusmod tempor incididunt ut labore.</p>
    <div class="more">READ MORE</div>
  </article>

  <article class="card abs" style="left:620px">
    <div class="photo" style="background:linear-gradient(#b8aa98,#f2f2f2)" role="img" aria-label="Modular cleanroom containment system"></div>
    <h3>Containment Systems</h3>
    <p>Lorem ipsum dolor sit amet, consect-etur adipisicing elit, sed do eiusmod tempor incididunt ut labore.</p>
    <div class="more">READ MORE</div>
  </article>
</section>

<div class="abs" style="left:0;top:843px;width:867px;height:1px;background:var(--line)"></div>

<section>
  <div class="abs" style="left:90px;top:866px;color:var(--navy)"><h2 class="sec-title">Manufacture Link</h2></div>
  <div class="rule abs" style="left:90px;top:890px;width:190px;background:var(--navy);color:var(--navy)"></div>
  <div class="partners abs">
    <div>Cleanfold</div><div>Tamworth Pumps</div><div>Fillwell</div><div>Norvale Plastics</div><div>K-Pod</div><div>Finary</div><div>Ardent Hose Co.</div>
  </div>
</section>

<footer class="footer abs">
  <div class="abs" style="left:90px;top:20px"><h2 class="sec-title">Contact Us</h2></div>
  <div class="rule abs" style="left:90px;top:43px;width:116px;background:#fff;color:#fff"></div>
  <div class="brand abs" style="left:90px;top:68px"><span class="dot"></span>Prairie Bio</div>
  <div class="abs" style="left:90px;top:112px;font-size:10.5px;font-weight:300">© Prairie Biosolutions, Corp.</div>
  <div class="social abs" style="left:90px;top:146px"><span></span><span></span><span></span><span></span><span></span></div>

  <div class="person abs" style="left:266px">
    <div class="photo" style="background:linear-gradient(#d9a36a,#b87a48)" role="img" aria-label="Portrait of sales contact Mark Dalton"></div>
    <h4>Mark Dalton</h4>
    <div class="line"><svg width="9" height="9" viewBox="0 0 9 9"><path d="M2 0l2 2-1 1.5 2.5 2.5L7 5l2 2-1.5 2C4 9 0 5 0 1.5z" fill="#fff"/></svg>(555) 014-5423</div>
    <div class="line"><svg width="10" height="8" viewBox="0 0 10 8"><rect x=".5" y=".5" width="9" height="7" fill="none" stroke="#fff"/><path d="M.5 .5 5 4.5 9.5 .5" fill="none" stroke="#fff"/></svg>mdalton@pr-bio.com</div>
  </div>

  <div class="person abs" style="left:384px">
    <div class="photo" style="background:linear-gradient(#9fb8cc,#3f8fd0)" role="img" aria-label="Portrait of sales contact Laura Benson"></div>
    <h4>Laura Benson</h4>
    <div class="line"><svg width="9" height="9" viewBox="0 0 9 9"><path d="M2 0l2 2-1 1.5 2.5 2.5L7 5l2 2-1.5 2C4 9 0 5 0 1.5z" fill="#fff"/></svg>(555) 019-7626</div>
    <div class="line"><svg width="10" height="8" viewBox="0 0 10 8"><rect x=".5" y=".5" width="9" height="7" fill="none" stroke="#fff"/><path d="M.5 .5 5 4.5 9.5 .5" fill="none" stroke="#fff"/></svg>lbenson@pr-bio.com</div>
  </div>

  <div class="field abs" style="left:502px;top:24px;width:216px;height:26px">Name :</div>
  <div class="field abs" style="left:502px;top:57px;width:216px;height:26px">Email :</div>
  <div class="field abs" style="left:502px;top:90px;width:275px;height:76px">Massage :</div>
  <div class="send abs" style="left:502px;top:173px;width:98px;height:27px">SEND</div>
</footer>

</body>
</html>
```